Bayward Vale Physiotherapy Website www.baywardvalephysiotherapy.com.au

Create Wordpress website for Bayward Vale Physiotherapy which aligns with our other locations www.oakmerephysiotherapy,com.au. We would like the website to present in a similar fashion to our exisiting site with similar headings and layout. We will then alter the text to make it location specific.

Coding

Coded - Design and coding required

Number of Pages Required

1 page

Font styles to use
Sans Serif

Requirements
Must have
• Colours of the website must match the colours of the colour Bayward Vale Physiotherapy logo
• Website must be complimentary to existing websites,
• www.oakmerephysiotherapy.com.au
• www.oakmerepilatesandrehab.com.au

```html
<!DOCTYPE html>
<html lang="en">
<head>
<meta charset="utf-8">
<title>Bayward Vale Physiotherapy</title>
<link href="https://fonts.googleapis.com/css2?family=Montserrat:wght@400;500;600;700&display=swap" rel="stylesheet">
<style>
:root{
  --navy:#252a5c;
  --green:#7fbaa0;
  --grey:#ebebeb;
  --text:#555a66;
  --white:#ffffff;
}
*{margin:0;padding:0;box-sizing:border-box}
html,body{width:1200px;height:2839px;overflow:hidden}
body{font-family:'Montserrat',sans-serif;color:var(--text);background:var(--white);position:relative}
.abs{position:absolute}
.center{text-align:center;left:0;width:1200px}

/* header */
.topline-green{left:0;top:0;width:574px;height:4px;background:var(--green)}
.topline-navy{left:574px;top:0;width:626px;height:4px;background:var(--navy)}
.brand{left:155px;top:38px;display:flex;align-items:center;gap:12px;font-size:21px;font-weight:700;color:var(--navy)}
.brand-dot{width:34px;height:34px;border-radius:50%;background:var(--navy)}
.help{left:632px;top:20px;display:flex;align-items:center;gap:10px;font-size:16px;color:#8a8f99}
.help strong{font-size:22px;color:var(--green);font-weight:500}
.help-socials{display:flex;gap:10px;margin-left:18px}
.soc{width:12px;height:12px;border-radius:50%;background:var(--navy);display:inline-block}
.nav{left:454px;top:76px;display:flex;gap:0;font-size:13px;font-weight:600;color:var(--navy)}
.nav span{margin-right:42px}
.nav span:last-child{margin-right:0}

/* hero */
.hero{left:0;top:117px;width:1200px;height:549px;background:linear-gradient(100deg,#e9eef2 0%,#f5f4f1 45%,#e7e2dc 75%,#cdbba6 100%)}
.hero-floor{left:0;top:540px;width:1200px;height:126px;background:linear-gradient(180deg,#d2b89a,#b8916b)}
.tag{left:454px;top:233px;width:303px;height:32px;background:var(--green);color:var(--white);font-size:22px;font-weight:500;text-align:center;line-height:32px;letter-spacing:.5px}
.headline{left:409px;top:271px;width:413px;height:51px;background:var(--navy);color:var(--white);font-size:40px;font-weight:600;text-align:center;line-height:51px}

/* section headings */
.sec-title{font-size:24px;font-weight:500;color:#1f2230;letter-spacing:.5px}
.sec-sub{display:flex;justify-content:center;align-items:center;gap:10px;font-size:10px;font-weight:600;color:var(--navy)}
.sec-sub i{display:block;width:58px;height:2px;background:var(--navy)}
.lead{font-size:12.5px;font-weight:600;color:#5a5f6a;line-height:23px}
.body{font-size:12.5px;line-height:18.5px;color:#6a6f7a}
.body p{margin-bottom:18px}

.book{left:511px;top:1071px;width:155px;height:40px;border-radius:6px;background:var(--navy);color:var(--white);font-size:12.5px;font-weight:600;text-align:center;line-height:40px}

/* services */
.services{left:0;top:1177px;width:1200px;height:538px;background:var(--grey)}
.card{width:256px;height:106px;border:3px solid var(--navy);background:var(--white);padding:22px 0 0 44px}
.card h3{font-size:13.5px;font-weight:700;color:#1f2230;margin-bottom:6px}
.card p{font-size:11px;line-height:13px;color:#2a2d38;white-space:nowrap;overflow:hidden;width:200px}
.icon{width:62px;height:62px;border-radius:50%;background:var(--navy)}
.icon.alt{background:var(--green)}

/* practitioners */
.person{width:240px;text-align:center}
.photo{width:156px;height:156px;border-radius:50%;border:4px solid var(--navy);margin:0 auto;background:linear-gradient(180deg,#e2e2e2,#9a9a9a)}
.person h4{font-size:12.5px;font-weight:700;color:var(--navy);margin-top:21px}
.person .role{font-size:12.5px;color:#555a66;margin-top:3px}
.person .bio{font-size:12.5px;line-height:18px;color:#6a6f7a;margin-top:2px}
.call{width:95px;height:27px;margin:20px auto 0;background:var(--green);color:var(--white);font-size:12px;line-height:27px}
.p-socials{display:flex;justify-content:center;gap:10px;margin-top:12px}
.p-socials .soc{width:10px;height:10px;background:#333}

/* contact */
.contact{left:0;top:2374px;width:1200px;height:431px;background:var(--navy);color:var(--white)}
.contact .sec-title{color:var(--white)}
.contact .sec-sub{color:var(--white)}
.contact .sec-sub i{background:var(--white)}
.c-col{width:320px;text-align:center}
.c-icon{width:46px;height:46px;border-radius:50%;background:var(--green);margin:0 auto;display:flex;align-items:center;justify-content:center}
.c-col h5{font-size:15px;font-weight:700;margin-top:30px;letter-spacing:.5px}
.c-col p{font-size:12.5px;line-height:18px;margin-top:20px}
.c-socials{display:flex;justify-content:center;gap:22px}
.c-socials .soc{width:20px;height:20px;background:var(--white)}
.footer{left:0;top:2805px;width:1200px;height:34px;background:var(--green);color:var(--white);font-size:11px;text-align:center;line-height:34px}
</style>
</head>
<body>

<header>
  <div class="abs topline-green"></div>
  <div class="abs topline-navy"></div>
  <div class="abs brand"><span class="brand-dot"></span>Bayward Vale Physiotherapy</div>
  <div class="abs help">
    <svg width="20" height="20" viewBox="0 0 24 24"><path fill="#7fbaa0" d="M6.6 10.8a15 15 0 0 0 6.6 6.6l2.2-2.2a1 1 0 0 1 1-.25 11.4 11.4 0 0 0 3.6.57 1 1 0 0 1 1 1V20a1 1 0 0 1-1 1A17 17 0 0 1 3 4a1 1 0 0 1 1-1h3.5a1 1 0 0 1 1 1c0 1.25.2 2.45.57 3.57a1 1 0 0 1-.25 1z"/></svg>
    Need Help? Call us: <strong>(888) 555-0190</strong>
    <span class="help-socials"><span class="soc"></span><span class="soc"></span><span class="soc"></span></span>
  </div>
  <nav class="abs nav"><span>HOME</span><span>ABOUT</span><span>SERVICE</span><span>CONDITIONS</span><span>HEALTH TIPS</span><span>BLOG</span><span>CONTACT</span></nav>
</header>

<section>
  <div class="abs hero" role="img" aria-label="Photo of a physiotherapist stretching a patient's leg on an exercise mat in a bright clinic"></div>
  <div class="abs hero-floor" role="img" aria-label="Clinic floor with exercise mat"></div>
  <div class="abs tag">A PASSION FOR HEALING</div>
  <div class="abs headline">MEDICAL CENTER</div>
</section>

<section>
  <h2 class="abs center sec-title" style="top:718px">WELCOME TO BAYWARD VALE PHYSIOTHERAPY</h2>
  <div class="abs center sec-sub" style="top:750px"><i></i>Bayward Vale Physiotherapy<i></i></div>
  <p class="abs lead" style="left:310px;width:580px;top:776px;text-align:center">Excepteur sint occaecat cupidatat non proident, sunt in culpa qui officia deserunt mollit anim id est laborum. Consect petur adipiscing elit.</p>
  <div class="abs body" style="left:205px;width:790px;top:843px;text-align:center">
    <p>Bayward Vale Physiotherapy is an innovative physiotherapy practice offering comprehensive services by experienced and highly-qualified physiotherapists.<br>We achieve outstanding clinical results for a broad range of common conditions including: back pain, neck pain, headache, migraine, shoulder pain, sports injuries, vertigo, knee pain, incontinence, persistent pelvic pain and women's health and men's health issues.</p>
    <p>Our team of physiotherapists have extensive experience from working in private practice, private and public hospitals, and research and teaching over a range of physiotherapy disciplines including sports, manipulative, musculoskeletal, neurological, pain management, continence, women's / men's health and paediatric services.</p>
    <p>We are confident our practice will offer a service that stands apart, as we value excellence in quality care delivered by highly-educated and experienced physiotherapists.</p>
  </div>
  <div class="abs book">BOOK ONLINE HERE</div>
</section>

<section>
  <div class="abs services"></div>
  <h2 class="abs center sec-title" style="top:1228px">OUR FEATURED SERVICE</h2>
  <div class="abs center sec-sub" style="top:1260px"><i></i>Bayward Vale Physiotherapy<i></i></div>
  <p class="abs lead" style="left:310px;width:580px;top:1286px;text-align:center">Excepteur sint occaecat cupidatat non proident, sunt in culpa qui officia deserunt mollit anim id est laborum. Consect petur adipiscing elit.</p>

  <div class="abs card" style="left:189px;top:1376px"><h3>PHYSIOTHERAPY</h3><p>Our team of experienced physiother-<br>apists have a wide range of speciali-</p></div>
  <div class="abs card" style="left:483px;top:1376px"><h3>CHRONIC PAIN MANAGMENT</h3><p>Our team of experienced physiother-<br>apists have a wide range of speciali-</p></div>
  <div class="abs card" style="left:778px;top:1376px"><h3>KNEE CLINIC</h3><p>Our team of experienced physiother-<br>apists have a wide range of speciali-</p></div>
  <div class="abs card" style="left:189px;top:1522px"><h3>REAL TIME ULTRASOUND</h3><p>Our team of experienced physiother-<br>apists have a wide range of speciali-</p></div>
  <div class="abs card" style="left:483px;top:1522px"><h3>WOMEN'S &amp; MEN'S HEALTH</h3><p>Our team of experienced physiother-<br>apists have a wide range of speciali-</p></div>
  <div class="abs card" style="left:778px;top:1522px"><h3>OTHER SERVICES</h3><p>Our team of experienced physiother-<br>apists have a wide range of speciali-</p></div>

  <div class="abs icon" style="left:153px;top:1398px" role="img" aria-label="Physiotherapy icon"></div>
  <div class="abs icon alt" style="left:447px;top:1398px" role="img" aria-label="Chronic pain icon"></div>
  <div class="abs icon" style="left:742px;top:1398px" role="img" aria-label="Knee clinic icon"></div>
  <div class="abs icon" style="left:153px;top:1544px" role="img" aria-label="Ultrasound icon"></div>
  <div class="abs icon" style="left:447px;top:1544px" role="img" aria-label="Women's and men's health icon"></div>
  <div class="abs icon" style="left:742px;top:1544px" role="img" aria-label="Other services icon"></div>
</section>

<section>
  <h2 class="abs center sec-title" style="top:1790px">OUR PRACTITIONERS</h2>
  <div class="abs center sec-sub" style="top:1822px"><i></i>Bayward Vale Physiotherapy<i></i></div>
  <p class="abs lead" style="left:310px;width:580px;top:1848px;text-align:center">Excepteur sint occaecat cupidatat non proident, sunt in culpa qui officia deserunt mollit anim id est laborum. Consect petur adipiscing elit.</p>

  <div class="abs person" style="left:126px;top:1951px">
    <div class="photo" role="img" aria-label="Portrait of Maren Holt"></div>
    <h4>MAREN HOLT</h4><div class="role">Director</div>
    <div class="bio">Maren completed her Bachelor of physiotherapy at the University of Eastvale in 2009 and more recently her Grade</div>
    <div class="call">Call Us</div>
    <div class="p-socials"><span class="soc"></span><span class="soc"></span><span class="soc"></span></div>
  </div>
  <div class="abs person" style="left:357px;top:1951px">
    <div class="photo" role="img" aria-label="Portrait of Dr Tessa Brindle"></div>
    <h4>DR TESSA BRINDLE</h4><div class="role">Director</div>
    <div class="bio">Maren completed her Bachelor of physiotherapy at the University of Eastvale in 2009 and more recently her Grade</div>
    <div class="call">Call Us</div>
    <div class="p-socials"><span class="soc"></span><span class="soc"></span><span class="soc"></span></div>
  </div>
  <div class="abs person" style="left:592px;top:1951px">
    <div class="photo" role="img" aria-label="Portrait of Claire Westbury"></div>
    <h4>CLAIRE WESTBURY</h4><div class="role">Director</div>
    <div class="bio">Maren completed her Bachelor of physiotherapy at the University of Eastvale in 2009 and more recently her Grade</div>
    <div class="call">Call Us</div>
    <div class="p-socials"><span class="soc"></span><span class="soc"></span><span class="soc"></span></div>
  </div>
  <div class="abs person" style="left:826px;top:1951px">
    <div class="photo" role="img" aria-label="Portrait of Owen Farrier"></div>
    <h4>OWEN FARRIER</h4><div class="role">B Pod M Physio</div>
    <div class="bio">Maren completed her Bachelor of physiotherapy at the University of Eastvale in 2009 and more recently her Grade</div>
    <div class="call">Call Us</div>
    <div class="p-socials"><span class="soc"></span><span class="soc"></span><span class="soc"></span></div>
  </div>
</section>

<footer>
  <div class="abs contact"></div>
  <h2 class="abs center sec-title" style="top:2428px;color:#fff">CONTACT US</h2>
  <div class="abs center sec-sub" style="top:2460px;color:#fff"><i style="background:#fff"></i>Bayward Vale Physiotherapy<i style="background:#fff"></i></div>

  <div class="abs c-col" style="left:103px;top:2534px;color:#fff">
    <div class="c-icon"><svg width="16" height="16" viewBox="0 0 24 24"><path fill="#fff" d="M12 2a7 7 0 0 0-7 7c0 5 7 13 7 13s7-8 7-13a7 7 0 0 0-7-7zm0 9.5A2.5 2.5 0 1 1 12 6.5a2.5 2.5 0 0 1 0 5z"/></svg></div>
    <h5>ADDRESS</h5>
    <p>Oakmere Pilates &amp; Rehab<br>42-44 Harlow Parade<br>Oakmere VIC 3099</p>
  </div>
  <div class="abs c-col" style="left:423px;top:2534px;color:#fff">
    <div class="c-icon"><svg width="16" height="16" viewBox="0 0 24 24"><path fill="#fff" d="M6.6 10.8a15 15 0 0 0 6.6 6.6l2.2-2.2a1 1 0 0 1 1-.25 11.4 11.4 0 0 0 3.6.57 1 1 0 0 1 1 1V20a1 1 0 0 1-1 1A17 17 0 0 1 3 4a1 1 0 0 1 1-1h3.5a1 1 0 0 1 1 1c0 1.25.2 2.45.57 3.57a1 1 0 0 1-.25 1z"/></svg></div>
    <h5>PHONE</h5>
    <p>+ 03 9555 0142, + 03 9555 0142,<br>+ 03 9555 0142.</p>
  </div>
  <div class="abs c-col" style="left:749px;top:2534px;color:#fff">
    <div class="c-icon"><svg width="18" height="14" viewBox="0 0 24 18"><rect x="1" y="1" width="22" height="16" rx="2" fill="none" stroke="#fff" stroke-width="2"/><path d="M1 2l11 8 11-8" fill="none" stroke="#fff" stroke-width="2"/></svg></div>
    <h5>ADDRESS</h5>
    <p>admin@oakmerepilatesandrehab.com.au<br>info@oakmerepilatesandrehab.com.au</p>
  </div>

  <div class="abs center c-socials" style="top:2757px"><span class="soc" style="background:#fff"></span><span class="soc" style="background:#fff"></span><span class="soc" style="background:#fff"></span></div>
  <div class="abs footer">© Copyright 2018 bayward vale physiotherapy | All Rights Reserved</div>
</footer>

</body>
</html>
```